Concierge Dental / Medical Supply Ordering Business - Sleek, Efficient, Professional, Elite

www.brantonkeelmedical.com - example website.

We are a concierge supply ordering business for medical and dental that provide DSO price savings on supplies while maintaining business autonomy and independence.

We want a very simple website that looks very professional says what we do and gives a very simple method to contact us & sign up as above.

Target Market(s)

Independent Dental and Medical Practices

Industry/Entity Type

Dental and Medical - healthcare

Coding

Coded - Design and coding required

Number of Pages Required

3 page

Font styles to use
Sans Serif

Colors
0054AA
0677BA
7BADD7
CADEEF
E8F1F8

Requirements
Must have
• Simple contact page, sleek efficient design, uncomplicated.
Nice to have
• Sign up page vs just a contact page.
Should not have
• Lots of pages, hard to navigate,

```html
<!DOCTYPE html>
<html lang="en">
<head>
<meta charset="utf-8">
<title>Clearpath Dental Supply</title>
<link rel="stylesheet" href="https://fonts.googleapis.com/css2?family=Outfit:wght@400;500;600&family=Figtree:ital,wght@0,400;0,500;0,600;1,400&display=swap">
<style>
:root{
  --navy:#1f5a8f;
  --blue:#0677ba;
  --deep:#0054aa;
  --sky:#6fcdf2;
  --mist:#7badd7;
  --pale:#cadeef;
  --ice:#e8f1f8;
  --ink:#111418;
  --text:#2b2f33;
  --grey:#6d737a;
  --footer:#1c1c1c;
  --white:#ffffff;
}
*{margin:0;padding:0;box-sizing:border-box}
html,body{width:1200px;height:3589px;overflow:hidden}
body{position:relative;background:var(--white);font-family:"Figtree",sans-serif;color:var(--text)}
.abs{position:absolute}
h1,h2,h3,h4{font-family:"Outfit",sans-serif;font-weight:500}

/* hero */
.hero{left:0;top:0;width:1200px;height:516px;background:linear-gradient(100deg,#2d4d6c 0%,#4f7a9c 45%,#6f95b3 70%,#3e6383 100%)}
.brand{display:flex;align-items:center;gap:10px;color:var(--white);font-family:"Figtree",sans-serif;font-weight:600}
.brand-mark{width:26px;height:26px;background:var(--white);border-radius:4px}
.hero .brand{left:111px;top:52px;font-size:17px}
.nav{right:114px;top:50px;display:flex;gap:30px}
.nav a{color:var(--white);text-decoration:none;font-size:15.5px;font-family:"Outfit",sans-serif}
.welcome{left:111px;top:234px;color:var(--sky);font-size:38px}
.hero-title{left:111px;top:282px;color:var(--white);font-size:58px;font-weight:500;letter-spacing:-.3px}

/* about */
.about-title{left:111px;top:578px;width:620px;font-size:34px;line-height:44px;color:var(--ink)}
.about-text{left:111px;top:684px;width:590px;font-size:16px;line-height:30px;color:var(--text)}
.about-text p+p{margin-top:30px}
.btn{display:flex;align-items:center;justify-content:center;font-family:"Outfit",sans-serif;font-weight:500;font-size:15.5px;text-decoration:none}
.btn-sky{background:var(--sky);color:var(--ink)}
.about-btn{left:111px;top:985px;width:152px;height:52px}
.about-photo{left:744px;top:584px;width:343px;height:482px;background:linear-gradient(135deg,#7aa6c8 0%,#c9dbe8 45%,#a88a78 100%)}

/* practice */
.practice{left:0;top:1136px;width:1200px;height:984px;background:linear-gradient(135deg,#6bbfe8 0%,#3c8cc7 45%,#2f6fa9 75%,#4b8ec4 100%)}
.practice-title{left:0;top:1200px;width:1200px;text-align:center;color:var(--white);font-size:36px}
.card{left:197px;width:807px;height:204px;background:var(--white);border-radius:8px}
.card-photo{position:absolute;top:8px;width:196px;height:188px;border-radius:3px}
.card-body{position:absolute;top:24px;width:540px}
.card-body h3{font-size:21px;color:var(--ink);margin-bottom:12px}
.card-body p{font-size:14px;line-height:30px;color:var(--text)}
.card-body a{display:block;margin-top:6px;font-family:"Outfit",sans-serif;font-size:13px;color:var(--sky);text-decoration:none;font-weight:500}
.view-all{left:525px;top:1981px;width:152px;height:50px;background:var(--navy);color:var(--white)}

/* testimonials */
.quote-badge{left:569px;top:2204px;width:62px;height:62px;border-radius:50%;background:linear-gradient(180deg,#3d8fc7,#2a6aa4)}
.test-title{left:0;top:2274px;width:1200px;text-align:center;font-size:40px;color:var(--ink)}
.test-lead{left:290px;top:2336px;width:620px;text-align:center;font-size:13.5px;line-height:26px;color:var(--text)}
.tcard{top:2428px;background:var(--white);border-radius:6px;box-shadow:0 8px 30px rgba(40,60,90,.09);padding:26px 24px}
.tcard p{font-style:italic;font-size:13.5px;line-height:25.5px;color:var(--grey)}
.person{display:flex;align-items:center;gap:12px;margin-top:26px}
.avatar{width:52px;height:52px;border-radius:50%;background:linear-gradient(180deg,#d9d2cc,#9c938c)}
.person h4{font-size:19px;color:var(--navy)}
.person span{font-size:14px;color:var(--grey)}
.faded{opacity:.35}
.dots{left:593px;top:2763px;display:flex;gap:6px}
.dots i{width:10px;height:10px;border-radius:50%;background:#c4c9cf;display:block}
.dots i:first-child{background:var(--navy)}

/* footer */
.footer{left:0;top:3096px;width:1200px;height:493px;background:var(--footer)}
.touch{left:139px;top:2877px;width:922px;height:312px;border-radius:22px;background:linear-gradient(180deg,#2f6da8,#275f98);text-align:center;color:var(--white)}
.touch h2{font-size:36px;margin-top:62px}
.touch p{font-style:italic;font-size:14.5px;line-height:26px;margin:14px auto 0;width:500px}
.touch .btn{width:152px;height:51px;margin:34px auto 0}
.foot-brand{left:118px;top:3330px;font-size:18px}
.socials{left:142px;top:3424px;display:flex;gap:9px}
.socials i{display:block;width:25px;height:25px;border-radius:50%;background:var(--white)}
.socials i:first-child{background:#3f8fd8}
.news{left:372px;top:3280px;width:290px;color:var(--white);text-align:center}
.news h4{font-size:19px;font-weight:600;margin-left:-10px}
.news p{font-size:14.5px;line-height:26px;margin-top:14px}
.news-field{left:378px;top:3391px;width:272px;height:41px;border-radius:21px;background:var(--white)}
.news-field span{position:absolute;left:22px;top:11px;font-size:14px;color:#9aa0a6}
.news-field svg{position:absolute;right:3px;top:3px}
.links{width:200px;color:var(--white);text-align:center}
.links h4{font-size:19px;font-weight:600;margin-bottom:12px}
.links a{display:block;color:var(--white);text-decoration:none;font-size:15px;line-height:30.5px}
.rule{left:118px;top:3503px;width:982px;height:1px;background:#333}
.copy{left:0;top:3535px;width:1200px;text-align:center;color:var(--white);font-size:15px}
</style>
</head>
<body>

<header class="abs hero" role="img" aria-label="Photo of a bright modern dental treatment room with a patient chair and cabinetry"></header>
<div class="abs brand"><span class="brand-mark"></span>Clearpath Dental Supply</div>
<nav class="abs nav">
  <a href="#">Home</a><a href="#">About</a><a href="#">Areas of Practice</a><a href="#">FAQs</a><a href="#">Contact Us</a>
</nav>
<h2 class="abs welcome">Welcome To</h2>
<h1 class="abs hero-title">Clearpath Dental Supply</h1>

<section>
  <h2 class="abs about-title">Advocating for financial transparency in the medical supply world.</h2>
  <div class="abs about-text">
    <p>Lorem ipsum dolor sit amet, consectetur adipiscing elit, sed do eiusmod tempor incididunt ut labore et dolore magna aliqua. Ut enim ad minim veniam, quis nostrud exercitation ullamco laboris nisi ut aliquip ex ea commodo consequat. Duis aute irure dolor in reprehenderit in voluptate velit esse cillum dolore eu fugiat nulla pariatur.</p>
    <p>Lorem ipsum dolor sit amet, consectetur adipiscing elit, sed do eiusmod tempor incididunt ut labore et dolore magna aliqua. Ut enim ad minim veniam, quis nostrud exercitation</p>
  </div>
  <a class="abs btn btn-sky about-btn" href="#">Learn More</a>
  <div class="abs about-photo" role="img" aria-label="Photo of a smiling young girl in a dental chair giving a gloved high five"></div>
</section>

<section>
  <div class="abs practice" role="img" aria-label="Soft blue background photo of a laboratory"></div>
  <h2 class="abs practice-title">Areas of Practice</h2>

  <article class="abs card" style="top:1283px">
    <div class="card-photo" style="left:8px;background:linear-gradient(180deg,#b9cde0,#4d6780)" role="img" aria-label="Photo of a modern distribution warehouse"></div>
    <div class="card-body" style="left:233px">
      <h3>Distribution</h3>
      <p>Lorem ipsum dolor sit amet, consectetur adipiscing elit, sed do eiusmod tempor incididunt ut labore et dolore magna aliqua. Quis ipsum suspendisse ultrices gravida.</p>
      <a href="#">Learn More</a>
    </div>
  </article>

  <article class="abs card" style="top:1515px">
    <div class="card-body" style="left:40px">
      <h3>Pharma</h3>
      <p>Lorem ipsum dolor sit amet, consectetur adipiscing elit, sed do eiusmod tempor incididunt ut labore et dolore magna aliqua. Quis ipsum suspendisse ultrices gravida.</p>
      <a href="#">Learn More</a>
    </div>
    <div class="card-photo" style="right:8px;background:linear-gradient(135deg,#1d4f8a,#5aa0d8)" role="img" aria-label="Photo of pharmaceutical vials on a production line"></div>
  </article>

  <article class="abs card" style="top:1743px">
    <div class="card-photo" style="left:8px;background:linear-gradient(135deg,#2a3d6a,#a8b9dc)" role="img" aria-label="Photo of medicine bottles in a row"></div>
    <div class="card-body" style="left:233px">
      <h3>Capital Equipment</h3>
      <p>Lorem ipsum dolor sit amet, consectetur adipiscing elit, sed do eiusmod tempor incididunt ut labore et dolore magna aliqua. Quis ipsum suspendisse ultrices gravida.</p>
      <a href="#">Learn More</a>
    </div>
  </article>

  <a class="abs btn view-all" href="#">View All</a>
</section>

<section>
  <div class="abs quote-badge">
    <svg width="62" height="62" viewBox="0 0 62 62"><text x="31" y="47" text-anchor="middle" font-family="Georgia,serif" font-size="40" font-weight="700" fill="#fff">“</text></svg>
  </div>
  <h2 class="abs test-title">Clients Testimonials</h2>
  <p class="abs test-lead">Lorem ipsum dolor sit amet, consectetur adipiscing elit, sed do eiusmod tempor incididunt ut labore et dolore magna aliqua. Quis ipsum suspendisse ultrices gravida.</p>

  <div class="abs tcard faded" style="left:-240px;width:411px;height:196px">
    <p>Lorem ipsum dolor sit amet, consectetur adipiscing elit, sed do eiusmod tempor incididunt ut labore et dolore magna aliqua. Quis ipsum suspendisse ultrices gravida. Risus com-</p>
  </div>
  <div class="abs tcard" style="left:192px;width:409px;height:286px">
    <p>Lorem ipsum dolor sit amet, consectetur adipiscing elit, sed do eiusmod tempor incididunt ut labore et dolore magna aliqua. Quis ipsum suspendisse ultrices gravida. Risus commodo viverra maecenas accumsan lacus vel facilisis.</p>
    <div class="person" style="margin-top:36px"><div class="avatar" role="img" aria-label="Client portrait"></div><div><h4>Devin Marlow</h4><span>Lorem Ipsum</span></div></div>
  </div>
  <div class="abs tcard" style="left:622px;width:408px;height:248px">
    <p>Lorem ipsum dolor sit amet, consectetur adipiscing elit, sed do eiusmod tempor incididunt ut labore et dolore magna aliqua. Quis ipsum suspendisse ultrices gravida. Risus commodo viverra maecenas accumsan lacus vel facilisis. Lorem ipsum dolor sit amet,</p>
    <div class="person" style="margin-top:10px"><div class="avatar" role="img" aria-label="Client portrait"></div><div><h4>Noelle T</h4><span>Lorem Ipsum</span></div></div>
  </div>
  <div class="abs tcard faded" style="left:1051px;width:408px;height:196px">
    <p>Lorem ipsum dolor sit amet, consectetur adipiscing elit, sed do eiusmod tempor incididunt ut labore et dolore magna aliqua. Quis ipsum suspendisse</p>
    <div class="person" style="margin-top:10px"><div class="avatar" role="img" aria-label="Client portrait"></div><div><h4>Corinne</h4><span>Lorem Ipsum</span></div></div>
  </div>

  <div class="abs dots"><i></i><i></i><i></i></div>
</section>

<footer>
  <div class="abs footer"></div>
  <div class="abs touch" role="region" aria-label="Get in touch">
    <h2>Get in Touch</h2>
    <p>For all questions, inquires regarding our services, or assistance in referring someone to us. Please contact us below.</p>
    <a class="btn btn-sky" href="#">Contact Us</a>
  </div>

  <div class="abs brand foot-brand"><span class="brand-mark"></span>Clearpath Dental Supply</div>
  <div class="abs socials"><i></i><i></i><i></i><i></i></div>

  <div class="abs news">
    <h4>Subscribe To Our Newsletter</h4>
    <p>Lorem ipsum dolor sit amet, consectetur adipiscing elit, sed do</p>
  </div>
  <div class="abs news-field">
    <span>Enter Your Email</span>
    <svg width="35" height="35" viewBox="0 0 35 35"><circle cx="17.5" cy="17.5" r="17.5" fill="#1f5a8f"/><path d="M10 18 L25 11 L20 25 L17 19 Z" fill="#fff"/></svg>
  </div>

  <div class="abs links" style="left:702px;top:3278px">
    <h4>Support</h4>
    <a href="#">Terms &amp; Conditions</a><a href="#">Privacy Policy</a><a href="#">About Us</a><a href="#">Support</a>
  </div>
  <div class="abs links" style="left:902px;top:3278px">
    <h4>Quick Links</h4>
    <a href="#">Home</a><a href="#">About</a><a href="#">Areas of Practice</a><a href="#">FAQs</a><a href="#">Contact Us</a>
  </div>

  <div class="abs rule"></div>
  <p class="abs copy">©Copyrights 2023&nbsp; Clearpath Dental Supply &nbsp;&nbsp;|&nbsp;&nbsp; All Rights Reserved</p>
</footer>

</body>
</html>
```